Redesign current business card for food company

i would like to redesign my business card. our company is food company, our product range from chips, juices, milk and etc (mostly dried food stuff).
I want o keep same logo but , the rest is open to new design.
you can check at our website about our company www.orvelpantry.com

Target Market(s)

most of food company

Industry/Entity Type

Business

Contact Information for Business Card

I want to keep more to blue color...

Colors
3176b5
abd036

Requirements
Must have
• our old logo
Nice to have
• we do not mind to have nice material on bus card in order to accomplish nice design. for example: using spot uv, embossed and etc.

```html
<!DOCTYPE html>
<html lang="en">
<head>
<meta charset="utf-8">
<title>Orvel Enterprises — Business Card</title>
<link rel="stylesheet" href="https://fonts.googleapis.com/css2?family=Open+Sans:wght@400;600;700&display=swap">
<style>
  :root {
    --bg: #e9e6e1;
    --card-white: #ffffff;
    --brand-blue: #1f8fd6;
    --brand-blue-deep: #1a6fc0;
    --accent-orange: #f7a823;
    --accent-yellow: #ffd21f;
    --text-blue: #1f86cf;
    --visual-light: #f4f1ea;
    --visual-mid: #e6e2d8;
  }
  * { box-sizing: border-box; margin: 0; padding: 0; }
  html, body { width: 1200px; height: 900px; overflow: hidden; }
  body {
    background: var(--bg);
    font-family: "Open Sans", Arial, sans-serif;
    position: relative;
  }
  .card {
    position: absolute;
    left: 270px;
    width: 660px;
    height: 377px;
    overflow: hidden;
    box-shadow: 0 4px 14px rgba(0,0,0,0.18);
  }
  .card-back {
    top: 46px;
    background: repeating-linear-gradient(180deg, #262626 0 2px, #1e1e1e 2px 4px);
    display: flex;
    align-items: center;
    justify-content: center;
  }
  .brand-name {
    font-family: "Open Sans", Arial, sans-serif;
    font-weight: 700;
    font-size: 128px;
    letter-spacing: -2px;
    color: var(--brand-blue);
    line-height: 1;
  }
  .card-front {
    top: 477px;
    background: var(--card-white);
  }
  .person {
    position: absolute;
    left: 22px;
    top: 20px;
    display: flex;
    gap: 10px;
    align-items: flex-start;
  }
  .person-mark {
    width: 34px;
    height: 34px;
    background: var(--brand-blue);
    flex: none;
  }
  .person-name {
    font-size: 22px;
    font-weight: 600;
    color: var(--accent-orange);
    line-height: 1.1;
  }
  .person-title {
    font-size: 14px;
    color: var(--text-blue);
  }
  .company {
    position: absolute;
    left: 56px;
    top: 84px;
    color: var(--text-blue);
    font-size: 15px;
    line-height: 1.3;
  }
  .company-name { font-size: 18px; font-weight: 600; }
  .contacts {
    position: absolute;
    left: 36px;
    top: 168px;
    list-style: none;
    color: var(--text-blue);
    font-size: 16px;
    line-height: 25px;
  }
  .contacts li { display: flex; align-items: center; gap: 12px; }
  .contacts svg { width: 14px; height: 14px; flex: none; }
  .contacts .web { color: var(--brand-blue-deep); }
  .food-visual {
    position: absolute;
    left: 380px;
    top: 60px;
    width: 250px;
    height: 250px;
    background: linear-gradient(180deg, var(--visual-light), var(--visual-mid));
  }
  .bands { position: absolute; left: 0; bottom: 0; width: 660px; height: 90px; }
</style>
</head>
<body>
  <section class="card card-back">
    <span class="brand-name">orvel</span>
  </section>

  <section class="card card-front">
    <div class="person">
      <span class="person-mark"></span>
      <div>
        <p class="person-name">Daniel Merriwether</p>
        <p class="person-title">President</p>
      </div>
    </div>

    <div class="company">
      <p class="company-name">Orvel Enterprises Corp.</p>
      <p>2470 Fenwick St. Alder Bay</p>
      <p>CA 90000</p>
    </div>

    <ul class="contacts">
      <li>
        <svg viewBox="0 0 14 14"><path fill="#f7a823" d="M3 1l2.5 3-1.5 1.5a8 8 0 0 0 4.5 4.5L10 8.5l3 2.5-1.5 2C6 13 1 8 1 2.5z"/></svg>
        <span>555 014 2388</span>
      </li>
      <li>
        <svg viewBox="0 0 14 14"><rect x="1" y="5" width="12" height="8" rx="1" fill="#f7a823"/><rect x="4" y="1" width="6" height="5" fill="#f7a823"/><rect x="3" y="8" width="8" height="1.5" fill="#fff"/></svg>
        <span>555 014 2377</span>
      </li>
      <li>
        <svg viewBox="0 0 14 14"><rect x="3" y="1" width="8" height="12" rx="1.5" fill="#f7a823"/><rect x="4.5" y="2.5" width="5" height="7" fill="#fff"/></svg>
        <span>555 017 4610</span>
      </li>
      <li>
        <svg viewBox="0 0 14 14"><rect x="1" y="3" width="12" height="8" fill="#f7a823"/><path d="M1 3l6 5 6-5" fill="none" stroke="#fff" stroke-width="1.2"/></svg>
        <span>Daniel@orvelpantry.com</span>
      </li>
      <li>
        <svg viewBox="0 0 14 14"><circle cx="7" cy="7" r="6" fill="#f7a823"/><path d="M1 7h12M7 1c-3 3-3 9 0 12M7 1c3 3 3 9 0 12" fill="none" stroke="#fff" stroke-width="1"/></svg>
        <span class="web">www.orvelpantry.com</span>
      </li>
    </ul>

    <div class="food-visual" role="img" aria-label="Food illustration: crackers, fruit and a milk splash"></div>

    <svg class="bands" viewBox="0 0 660 90" preserveAspectRatio="none">
      <defs>
        <linearGradient id="band-yellow" x1="0" x2="0" y1="0" y2="1">
          <stop offset="0" stop-color="#ffd21f"/>
          <stop offset="1" stop-color="#f7a823"/>
        </linearGradient>
        <linearGradient id="band-blue" x1="0" x2="0" y1="0" y2="1">
          <stop offset="0" stop-color="#2aa3e6"/>
          <stop offset="1" stop-color="#1a6fc0"/>
        </linearGradient>
      </defs>
      <polygon points="0,8 300,36 285,58 0,38" fill="url(#band-yellow)"/>
      <polygon points="310,40 660,70 660,90 285,90" fill="url(#band-blue)"/>
    </svg>
  </section>
</body>
</html>
```